BOLD & MINIMALIST DESIGN NEEDED

We want a very bold but minimalistic business card design that is impactful and utilizes both sides of the business card. Our current logo is included for your use.

We want bold fonts and good use of negative space. We don't want the logo to overpower the design.

Target Market(s)

Professionals who are building new commercial buildings.

Industry/Entity Type

Construction

Contact Information for Business Card

Name, Title, email, office phone, cell phone, website

Font styles to use
Serif
Sans Serif

Requirements
Must have
• Bold design!

```html
<!DOCTYPE html>
<html lang="en">
<head>
<meta charset="utf-8">
<title>Ridgeline Design + Build — Business Card</title>
<link href="https://fonts.googleapis.com/css2?family=Montserrat:wght@400;500;800&display=swap" rel="stylesheet">
<style>
  :root {
    --backdrop: #2f2f2f;
    --brand-green: #86c442;
    --paper: #ffffff;
    --ink: #111111;
    --card-w: 540px;
    --card-h: 310px;
  }
  * { box-sizing: border-box; margin: 0; padding: 0; }
  html, body {
    width: 1200px; height: 689px; overflow: hidden;
    background: var(--backdrop);
    font-family: "Montserrat", Arial, sans-serif;
  }
  .stage {
    position: relative; width: 1200px; height: 689px;
    display: flex; align-items: center; justify-content: center; gap: 40px;
  }
  .card {
    position: relative; width: var(--card-w); height: var(--card-h);
    border-radius: 22px; overflow: hidden;
  }
  /* Front */
  .card-front {
    background: var(--brand-green);
    display: flex; flex-direction: column; align-items: center; justify-content: center;
    color: var(--paper);
  }
  .wordmark { font-weight: 800; text-align: center; line-height: 1; }
  .wordmark-name { display: block; font-size: 64px; letter-spacing: 1px; }
  .wordmark-tagline { display: block; font-size: 17px; letter-spacing: 9px; margin-top: 12px; }
  /* Back */
  .card-back { background: var(--paper); }
  .back-shape { position: absolute; inset: 0; width: 100%; height: 100%; }
  .back-wordmark {
    position: absolute; left: 0; width: 420px; top: 58px; color: var(--ink);
  }
  .back-wordmark .wordmark-name { font-size: 44px; }
  .back-wordmark .wordmark-tagline { font-size: 12px; letter-spacing: 6px; margin-top: 8px; }
  .person {
    position: absolute; left: 34px; top: 238px; color: var(--paper);
  }
  .person-name { font-weight: 800; font-size: 27px; letter-spacing: 0.5px; }
  .person-title { font-weight: 400; font-size: 13px; letter-spacing: 1px; margin-top: 4px; text-align: right; }
  .divider {
    position: absolute; left: 300px; top: 200px; width: 1.5px; height: 90px;
    background: var(--paper);
  }
  .contact-list {
    position: absolute; left: 318px; top: 196px; list-style: none; color: var(--paper);
    font-size: 13px; font-weight: 500;
  }
  .contact-list li { display: flex; align-items: center; gap: 8px; height: 22px; }
  .contact-list svg { width: 13px; height: 13px; fill: var(--paper); flex: none; }
</style>
</head>
<body>
<main class="stage">
  <section class="card card-front" aria-label="Card front">
    <h1 class="wordmark">
      <span class="wordmark-name">RIDGELINE</span>
      <span class="wordmark-tagline">DESIGN + BUILD</span>
    </h1>
  </section>

  <section class="card card-back" aria-label="Card back">
    <svg class="back-shape" viewBox="0 0 540 310" preserveAspectRatio="none" aria-hidden="true">
      <path d="M0 250 Q300 236 540 58 L540 310 L0 310 Z" fill="var(--brand-green)"/>
      <path d="M40 240 Q300 222 500 72 Q320 232 40 244 Z" fill="var(--ink)"/>
    </svg>

    <div class="wordmark back-wordmark">
      <span class="wordmark-name">RIDGELINE</span>
      <span class="wordmark-tagline">DESIGN + BUILD</span>
    </div>

    <div class="person">
      <p class="person-name">MARCUS HALE</p>
      <p class="person-title">OWNER-CEO</p>
    </div>

    <div class="divider"></div>

    <ul class="contact-list">
      <li>
        <svg viewBox="0 0 16 16"><path d="M3 1h3l1.5 4-2 1.2a9 9 0 0 0 4.3 4.3L11 8.5l4 1.5v3a2 2 0 0 1-2 2A12 12 0 0 1 1 3a2 2 0 0 1 2-2z"/></svg>
        555 010 2040
      </li>
      <li>
        <svg viewBox="0 0 16 16"><path d="M4.5 0h7A1.5 1.5 0 0 1 13 1.5v13a1.5 1.5 0 0 1-1.5 1.5h-7A1.5 1.5 0 0 1 3 14.5v-13A1.5 1.5 0 0 1 4.5 0zM4.5 2v10h7V2zM8 13a1 1 0 1 0 0 2 1 1 0 0 0 0-2z"/></svg>
        555 010 3175
      </li>
      <li>
        <svg viewBox="0 0 16 16"><path d="M1 3h14v10H1zM2 4.2v.4l6 4.2 6-4.2v-.4z"/></svg>
        info@ridgelinebuild.com
      </li>
      <li>
        <svg viewBox="0 0 16 16"><path d="M8 0a8 8 0 1 0 0 16A8 8 0 0 0 8 0zm0 1.5c.9 0 2 1.9 2.3 5H5.7C6 3.4 7.1 1.5 8 1.5zM5.7 8h4.6c-.3 3.1-1.4 6.5-2.3 6.5S6 11.1 5.7 8zM1.6 6.5a6.5 6.5 0 0 1 3.1-4.1A11 11 0 0 0 4.2 6.5zm0 1.5h2.6c.1 2.3.6 4.3 1.5 5.6A6.5 6.5 0 0 1 1.6 8zm9.8-1.5a11 11 0 0 0-.5-4.1 6.5 6.5 0 0 1 3.5 4.1zm0 1.5h3a6.5 6.5 0 0 1-4.1 5.6c.9-1.3 1-3.3 1.1-5.6z"/></svg>
        www.ridgelinebuild.com
      </li>
    </ul>
  </section>
</main>
</body>
</html>
```